Business card design for web travel company

Hi
we'd like to receive some proposal for a business card design.
Stayvora is a private travel club, dedicated to all travel lovers, with unique offers for exclusive destinations all around the world. At Stayvora you can find a wide range of offers for resorts, boutique hotels and travel packages at the best guaranteed price available on the market. The convenience of the offer is guaranteed by a private sales model: offers are available for a limited time only and they are personally chosen by Stayvora's qualified team of travel experts.
We offer only exclusive hotels with discounted prices but we are not an outlet or a discount supermarket: the design should reflect our connection with luxury, exclusivity using the same style of our website www.stayvora-example.com.
We want to make sure that when we'll present ourself to our business partner they will feel immediately which is our brand positioning giving them also a sense of an affordable and reliable partner.
In attachment you can also find our brand guidelines (please note that we are NOT USING ANY MORE THE TAG LINE "Five star outlet" mentioned in it).
The info to be inserted are:
Name Surname
Job Title
Tel
Mobile (when needed)
Email
Stayvora S.r.l.
Via Bruno Salvi 27
20139 Milano

```html
<!DOCTYPE html>
<html lang="en">
<head>
<meta charset="utf-8">
<title>Stayvora business card</title>
<link rel="stylesheet" href="https://fonts.googleapis.com/css2?family=Exo+2:wght@300;600&display=swap">
<style>
  :root {
    --page: #e8e5e1;
    --card-black: #050505;
    --card-white: #ffffff;
    --ink: #1d1d1d;
    --light: #ffffff;
    --muted: #c9c9c9;
    --gold: #b5a578;
    --edge: #3a3a3a;
  }
  * { margin: 0; padding: 0; box-sizing: border-box; }
  html, body { width: 1200px; height: 900px; overflow: hidden; }
  body {
    background: var(--page);
    font-family: "Exo 2", Arial, sans-serif;
    position: relative;
  }
  .card {
    position: absolute;
    top: 307px;
    width: 500px;
    height: 283px;
    border-radius: 14px;
    overflow: hidden;
    background: var(--card-black);
    box-shadow: 0 0 0 1px var(--edge);
  }
  .card--front { left: 75px; }
  .card--back { left: 623px; }
  .texture {
    position: absolute;
    inset: 0;
    background: linear-gradient(135deg, #0a0a0a 0%, #1a1a1a 55%, #0c0c0c 100%);
  }
  .front__brand-panel {
    position: absolute;
    left: 0; top: 0; bottom: 0;
    width: 246px;
    background: var(--card-white);
    display: flex;
    align-items: center;
    padding-left: 22px;
  }
  .brand-name {
    font-weight: 300;
    letter-spacing: 0.5px;
    line-height: 1;
  }
  .front__brand-panel .brand-name { font-size: 38px; color: var(--ink); }
  .front__contact {
    position: absolute;
    left: 281px;
    top: 115px;
    color: var(--light);
  }
  .contact__name {
    font-weight: 600;
    font-size: 21px;
    margin-bottom: 10px;
  }
  .contact__line {
    display: flex;
    align-items: center;
    gap: 5px;
    font-size: 12px;
    font-weight: 300;
    line-height: 17px;
  }
  .contact__line svg { width: 12px; height: 10px; flex: none; }
  .back__brand {
    position: absolute;
    left: 54px;
    top: 112px;
    color: var(--light);
  }
  .back__brand .brand-name { font-size: 48px; }
  .back__url {
    margin-top: 6px;
    font-size: 13px;
    font-weight: 300;
    letter-spacing: 2px;
    color: var(--muted);
  }
</style>
</head>
<body>
  <section class="card card--front" aria-label="Business card front">
    <div class="texture" role="img" aria-label="Fine diagonal line texture on black"></div>
    <div class="front__brand-panel">
      <span class="brand-name">Stayvora</span>
    </div>
    <div class="front__contact">
      <p class="contact__name">Marco Deltrani</p>
      <p class="contact__line">
        <svg viewBox="0 0 12 10" aria-hidden="true"><path fill="var(--gold)" d="M1 3 Q6 -1 11 3 L10 4.5 L8 4 L8 3 Q6 2.3 4 3 L4 4 L2 4.5 Z M3 5 L9 5 L10.5 9 L1.5 9 Z"/></svg>
        <span>: +23 4567 8910</span>
      </p>
      <p class="contact__line">
        <svg viewBox="0 0 12 10" aria-hidden="true"><rect x="0.7" y="1.2" width="10.6" height="7.6" fill="none" stroke="var(--gold)" stroke-width="1.2"/><path d="M0.7 1.2 L6 5.5 L11.3 1.2 M0.7 8.8 L4.5 4.5 M11.3 8.8 L7.5 4.5" fill="none" stroke="var(--gold)" stroke-width="1"/></svg>
        <span>: marco@stayvora-example.com</span>
      </p>
    </div>
  </section>

  <section class="card card--back" aria-label="Business card back">
    <div class="texture" role="img" aria-label="Fine diagonal line texture on black"></div>
    <div class="back__brand">
      <p class="brand-name">Stayvora</p>
      <p class="back__url">www.stayvora-example.com</p>
    </div>
  </section>
</body>
</html>
```